Web Design Project

i'm looking for a sleek modern design i can use for a web site that deals with.
Intelligent Data Capture
Accounts Payable Solutions for faster processing based on our scanning solution.
ultimately we are a intelligent scanning software.

here is a great website, that does exactly what we do, and we like to have most of their services and products.

so something in this idea would be great.
www.valtrino.com

so i guess i want a good landing/home page which is smartly designed so users will be inclined to leave their information.

and then information pages.

also i dont need any cms for you to include, i only need you to hook the html hooks for RANK Kettle as i already have a CMS and need it to hook in to that, i am including links to that cheat sheet.
so it is easier when included as you create the Theme.

http://www.rankkettle.com/how-to-create-website-template.html
http://www.rankkettle.com/cheat-sheet.html
Updates

Hi Guys sorry for the long pause in design, but here is where we stand.

what ever design i choose, i need that designer to customize a few things for me based on design that was designed.
and i will need designer to match that them to work with RANK Kettle
here is the cheat sheet for the hooks that we need to match and make it work.
if you have any questions let me know.

otherwise i look forward to working with you. and good luck.

Target Market(s)

CFO's AP Managers, mostly ppl who are not Tech freindly

Industry/Entity Type

Software

Requirements
Must have
• i need on home page, the rotating banner should have 1 ability to place youtube links to show videos, and also ability to add buttons on these rotating banners that will allow forms to pop up take to another page.

```html
<!DOCTYPE html>
<html lang="en">
<head>
<meta charset="utf-8">
<title>KESTA – Intelligent Data Capture</title>
<link href="https://fonts.googleapis.com/css2?family=PT+Sans+Narrow:wght@400;700&family=Source+Sans+3:wght@300;400;600;700&display=swap" rel="stylesheet">
<style>
:root{
  --brand:#2b4c98;
  --navy:#2c3f7f;
  --navy-deep:#22336c;
  --page-top:#4a5fa0;
  --page-bottom:#2f4383;
  --orange:#e8590c;
  --orange-bright:#f57a12;
  --yellow:#f2b705;
  --text:#4a5a8c;
  --muted:#6d7898;
  --rule:#d9dce6;
  --white:#fff;
}
*{box-sizing:border-box;margin:0;padding:0}
html,body{width:1152px;height:1200px;overflow:hidden}
body{font-family:"Source Sans 3",sans-serif;color:var(--text);
  background:linear-gradient(180deg,var(--page-top) 0,var(--page-bottom) 1088px,var(--navy-deep) 1088px)}
.page{position:relative;width:1152px;height:1200px}
a{color:inherit;text-decoration:none}

/* header */
.site-header{position:absolute;left:0;top:0;width:1152px;height:109px;
  background:linear-gradient(180deg,#fff 0,#fff 55%,#e6ebf6 100%);border-top:3px solid #d6dcec}
.brand{position:absolute;left:104px;top:30px}
.brand-name{font-family:"PT Sans Narrow",sans-serif;font-weight:700;font-size:46px;line-height:44px;color:var(--brand);letter-spacing:.5px}
.brand-slogan{font-size:12.5px;color:var(--brand);margin-left:11px;margin-top:-2px}
.search{position:absolute;left:673px;top:12px;width:194px;height:25px;border:1px solid #b9c1d6;background:#fff;
  font-size:11.5px;color:#666;padding:4px 8px}
.search svg{position:absolute;right:7px;top:8px}
.account-links{position:absolute;left:885px;top:17px;font-size:11.5px;color:var(--brand)}
.account-links span{color:#9aa4c0;margin:0 6px}
.main-nav{position:absolute;right:95px;top:73px;display:flex;font-size:15px;color:var(--brand)}
.main-nav a{padding:0 15px;border-left:1px solid #9fb0d6;line-height:17px}
.main-nav a:first-child{border-left:0}
.main-nav a:last-child{padding-right:0}

/* slider */
.hero{position:absolute;left:86px;top:120px;width:977px;height:332px;background:#fff;padding:3px;border-radius:2px}
.hero-inner{position:relative;width:100%;height:100%;overflow:hidden;
  background:linear-gradient(90deg,#eef1f8 0,#f3f5f9 38%,#dfe4ea 48%,#a8b2b8 62%,#6c747c 78%,#3b3f46 100%)}
.hero-photo{position:absolute;right:0;top:0;width:560px;height:100%}
.hero-copy{position:absolute;left:51px;top:56px;width:330px}
.hero-title{font-family:"PT Sans Narrow",sans-serif;font-weight:700;color:var(--navy);font-size:34px;line-height:36px}
.hero-title small{display:block;font-size:28px;line-height:34px}
.hero-sub{font-family:"PT Sans Narrow",sans-serif;font-weight:700;color:var(--orange-bright);font-size:19px;margin-top:9px}
.hero-text{font-size:13px;line-height:19px;color:#666;margin-top:8px;width:290px}
.btn-primary{display:inline-block;margin-top:14px;background:linear-gradient(#3c5aa6,#233e86);color:#fff;
  font-family:"PT Sans Narrow",sans-serif;font-weight:700;font-size:13px;padding:6px 20px;border-radius:3px}
.dots{display:flex;gap:4px;margin-top:19px}
.dots i{width:9px;height:9px;border-radius:50%;background:#c5cde0}
.dots i:first-child{background:var(--navy)}

/* content panel */
.content{position:absolute;left:86px;top:452px;width:977px;height:636px;background:#fff}
.features{position:absolute;left:28px;top:13px;display:flex;gap:17px}
.feature{width:217px}
.feature-photo{height:124px;border:1px solid #cfd4e0}
.feature h3{font-family:"PT Sans Narrow",sans-serif;font-weight:700;font-size:18px;color:var(--navy);margin:10px 0 6px 4px}
.feature p{font-size:11.5px;line-height:19px;color:var(--text);margin-left:3px}
.btn-yellow{display:inline-block;margin:6px 0 0 3px;background:var(--yellow);color:#fff;font-family:"PT Sans Narrow",sans-serif;
  font-weight:700;font-size:12px;padding:4px 13px;border-radius:2px}
.divider{position:absolute;left:27px;top:303px;width:917px;border-top:1px solid var(--rule)}
.section-title{font-size:19px;color:var(--orange);font-weight:400}
.welcome{position:absolute;left:30px;top:330px;width:560px}
.welcome .lead{font-weight:700;font-size:12px;line-height:20px;color:var(--navy);margin-top:10px}
.welcome p{font-size:11.5px;line-height:19px;margin-top:10px;color:var(--text)}
.videos{position:absolute;left:623px;top:330px}
.video{position:relative;margin-top:9px;width:333px;height:227px;border:4px solid #2b2b2b;
  background:linear-gradient(100deg,#5c6066 0,#9aa0a6 28%,#e5e8ec 50%,#f4f1e4 75%,#e9eef3 100%)}
.video svg{position:absolute;left:142px;top:88px}

/* footer */
.site-footer{position:absolute;left:0;top:1088px;width:1152px;height:112px;border-top:4px solid #6c7fb5;color:#fff}
.footer-nav{position:absolute;left:102px;top:19px;font-size:12.5px;display:flex;gap:16px}
.contact-line{position:absolute;left:705px;top:17px;font-size:12.5px}
.contact-line span{margin:0 5px}
.social{position:absolute;left:953px;top:16px;display:flex;gap:6px}
.social i{width:18px;height:18px;border-radius:2px;background:#3f64b0}
.social i:nth-child(3){background:#e8731c}
.social i:nth-child(4){background:#c4302b}
.footer-rule{position:absolute;left:107px;top:64px;width:952px;border-top:1px solid #43569a}
.copyright{position:absolute;left:108px;top:80px;font-size:11px;color:#c4cbe3}
</style>
</head>
<body>
<div class="page">
  <header class="site-header">
    <div class="brand">
      <div class="brand-name">KESTA</div>
      <div class="brand-slogan">Slogan goes here</div>
    </div>
    <div class="search">Search here..
      <svg width="5" height="7" viewBox="0 0 5 7"><path d="M0 0L5 3.5L0 7Z" fill="#666"/></svg>
    </div>
    <div class="account-links"><a href="#">Sign Up</a><span>|</span><a href="#">Login</a><span>|</span><a href="#">Member</a><span>|</span><a href="#">FAQ</a></div>
    <nav class="main-nav">
      <a href="#">Home</a><a href="#">About Us</a><a href="#">Technology</a><a href="#">Services</a><a href="#">News</a><a href="#">Video</a><a href="#">Support</a><a href="#">Contact</a>
    </nav>
  </header>

  <section class="hero">
    <div class="hero-inner">
      <div class="hero-photo" role="img" aria-label="Photo of two business women reviewing work on a laptop in a bright office"></div>
      <div class="hero-copy">
        <h1 class="hero-title">Intelligent Data Capture<small>from Online sites</small></h1>
        <div class="hero-sub">Pellentesque habitant morbi tristique</div>
        <p class="hero-text">Sed porta. Suspendisse quam leo, molestie sed, luctus quis, feugiat in, pede. Fusce tellus. Sed metus augue, convallis et, vehicula.</p>
        <a class="btn-primary" href="#">LEARN MORE</a>
        <div class="dots"><i></i><i></i><i></i><i></i></div>
      </div>
    </div>
  </section>

  <main class="content">
    <div class="features">
      <article class="feature">
        <div class="feature-photo" role="img" aria-label="Photo of a team gathered around a laptop" style="background:linear-gradient(135deg,#2f4f9c,#7d97cf 55%,#c9d3e6)"></div>
        <h3>What We Do</h3>
        <p>Lorem ipsum dolor sit amet, consectetuer adipiscing elit. Nam cursus. Morbi ut mi. Nullam enim leo, egestas id.</p>
        <a class="btn-yellow" href="#">LEARN MORE</a>
      </article>
      <article class="feature">
        <div class="feature-photo" role="img" aria-label="Photo of colleagues discussing work at a laptop" style="background:linear-gradient(135deg,#3b3f48,#8a8f98 55%,#d9dade)"></div>
        <h3>Why We Are</h3>
        <p>Lorem ipsum dolor sit amet, consectetuer adipiscing elit. Nam cursus. Morbi ut mi. Nullam enim leo, egestas id.</p>
        <a class="btn-yellow" href="#">LEARN MORE</a>
      </article>
      <article class="feature">
        <div class="feature-photo" role="img" aria-label="Photo of a business meeting around a table" style="background:linear-gradient(135deg,#e9ecf0,#c6ccd6 50%,#8f99aa)"></div>
        <h3>How we work</h3>
        <p>Lorem ipsum dolor sit amet, consectetuer adipiscing elit. Nam cursus. Morbi ut mi. Nullam enim leo, egestas id.</p>
        <a class="btn-yellow" href="#">LEARN MORE</a>
      </article>
      <article class="feature">
        <div class="feature-photo" role="img" aria-label="Photo of a man pointing at a computer monitor" style="background:linear-gradient(135deg,#f1f2f4,#cfd6e2 55%,#8aa0c6)"></div>
        <h3>Featured Services</h3>
        <p>Lorem ipsum dolor sit amet, consectetuer adipiscing elit. Nam cursus. Morbi ut mi. Nullam enim leo, egestas id.</p>
        <a class="btn-yellow" href="#">LEARN MORE</a>
      </article>
    </div>

    <div class="divider"></div>

    <section class="welcome">
      <h2 class="section-title">Welcome to Our Website Mainpage</h2>
      <p class="lead">Pellentesque habitant morbi tristique senectus et netus et malesuada fames ac turpis egestas. In posuere felis nec tortor. Pellentesque faucibus. Ut accumsan ultricies elit. Maecenas at justo id.</p>
      <p>Donec dictum lectus non odio. Cras a ante vitae enim iaculis aliquam. Mauris nunc quam, venenatis nec, euismod sit amet, egestas placerat, est. Pellentesque habitant morbi tristique senectus et netus et malesuada fames ac turpis egestas. Cras id elit. Integer quis urna. Ut ante enim, dapibus malesuada, fringilla eu, condimentum quis, tellus. Aenean porttitor eros vel dolor. Donec convallis pede venenatis nibh. Duis quam. Nam eget lacus. Aliquam erat volutpat. Quisque dignissim congue leo.</p>
      <p>Mauris vel lacus vitae felis vestibulum volutpat. Etiam est nunc, venenatis in, tristique eu, imperdiet ac, nisl. Cum sociis natoque penatibus et magnis dis parturient montes, nascetur ridiculus mus.</p>
    </section>

    <section class="videos">
      <h2 class="section-title">Recent Videos</h2>
      <div class="video" role="img" aria-label="Video still of a businessman in front of floating website screens">
        <svg width="50" height="50" viewBox="0 0 50 50"><circle cx="25" cy="25" r="24" fill="#1e1e1e"/><path d="M19 14L36 25L19 36Z" fill="#fff"/></svg>
      </div>
    </section>
  </main>

  <footer class="site-footer">
    <nav class="footer-nav">
      <a href="#">Home</a><a href="#">About us</a><a href="#">Technology</a><a href="#">Services</a><a href="#">News</a><a href="#">Video</a><a href="#">Support</a><a href="#">Contact</a>
    </nav>
    <div class="contact-line">Toll free: 800.555.0142<span>|</span>Fax 696.555.0187</div>
    <div class="social" aria-label="Social links"><i></i><i></i><i></i><i></i></div>
    <div class="footer-rule"></div>
    <div class="copyright">© 2012 Company Name.&nbsp; All right reserved.&nbsp; Term of Use</div>
  </footer>
</div>
</body>
</html>
```